Venture Capital Firm Needs Website Redesign

We need a bold revamp of our website (https://halverine.vc/)
which at the moment looks washed out. We want a crisp, fresh and unique look. Feel free to keep as much or as little content in the site. The only thing we need to keep is a team section. The site should convey a clear distinction between our 3 product lines: Venture Capital, Private Credit, and Crypto. Two versions of our logo are attached and they should not change. For design inspirations, we like http://www.9plm.com/ for a more simple site and for a more built out site we like http://bluetorch.com/

Updates
Industry/Entity Type
Investment
Coding
Coded - Design and coding required
Number of Pages Required
1 page
Font styles to use
Colors
Designer to choose colors to be used in the design.
Requirements
Must have
- - Clear distinction between our 3 product lines: Venture Capital, Private Credit
- - Team section

Nice to have
- Some really creative aspect like http://www.9plm.com/ has with the distinction between first, second, and third kind

```html
<!DOCTYPE html>
<html lang="en">
<head>
<meta charset="utf-8">
<title>Halverine</title>
<link href="https://fonts.googleapis.com/css2?family=Exo+2:wght@400;500;600&family=Arimo:wght@400;700&display=swap" rel="stylesheet">
<style>
:root{
  --hero-deep:#0b3f63;
  --hero-mid:#1877b0;
  --hero-light:#6cc4ef;
  --green:#85996b;
  --green-icon:#6f8f4c;
  --ink:#2b2b2b;
  --text:#3a3a3a;
  --page:#f3f4f6;
  --white:#ffffff;
  --team-dark:#3a3a3a;
  --team-mid:#6a6a6a;
}
*{box-sizing:border-box;margin:0;padding:0}
html,body{width:738px;height:1200px;overflow:hidden}
body{position:relative;background:var(--page);font-family:"Arimo",Arial,sans-serif;color:var(--text)}
.hero{position:absolute;left:0;top:0;width:738px;height:370px;
  background:linear-gradient(100deg,var(--hero-deep) 0%,var(--hero-mid) 45%,#0d5c8f 100%)}
.hero-visual{position:absolute;right:0;top:0;width:330px;height:370px;
  background:radial-gradient(ellipse at 60% 35%,var(--hero-light) 0%,rgba(108,196,239,.5) 35%,rgba(13,92,143,0) 75%)}
.brand{position:absolute;left:52px;top:24px;display:flex;align-items:center;gap:6px;
  font-family:"Exo 2",sans-serif;font-size:15px;font-weight:500;color:var(--white);letter-spacing:.5px}
.brand-dot{width:10px;height:10px;border:1.5px solid var(--white);border-radius:50%}
.nav{position:absolute;left:300px;top:20px;display:flex;gap:11px;
  font-family:"Exo 2",sans-serif;font-size:10.5px;font-weight:500;color:var(--white)}
.nav a{color:inherit;text-decoration:none;padding-bottom:3px}
.nav a.active{border-bottom:1px solid var(--white)}
.hero-title{position:absolute;left:62px;top:120px;width:330px;
  font-family:"Exo 2",sans-serif;font-weight:400;font-size:21px;line-height:31.5px;color:var(--white)}
.btn{display:inline-block;background:var(--green);color:var(--white);border-radius:14px;
  font-family:"Exo 2",sans-serif;font-weight:500;text-align:center}
.hero-btn{position:absolute;left:61px;top:233px;width:121px;height:26px;line-height:26px;font-size:10.5px}
.lines{position:absolute;left:68px;top:333px;width:602px;height:175px;background:var(--white);display:flex}
.line-item{flex:1;text-align:center;padding-top:14px;position:relative}
.line-item+.line-item::before{content:"";position:absolute;left:0;top:17px;bottom:20px;border-left:1px solid #e2e2e2}
.line-item svg{width:64px;height:52px}
.line-item h3{font-family:"Exo 2",sans-serif;font-weight:500;font-size:13px;color:var(--ink);margin-top:6px}
.line-item p{font-size:7px;line-height:12px;width:130px;margin:8px auto 0;color:var(--text)}
.about{position:absolute;left:70px;top:552px;width:600px;text-align:center}
.about h2{font-family:"Arimo",sans-serif;font-weight:700;font-size:21px;color:var(--ink)}
.about p{font-size:8.8px;line-height:17.3px;margin-top:10px;color:var(--text)}
.team{position:absolute;left:0;top:697px;width:738px;height:307px;text-align:center;color:var(--white)}
.team-photo{position:absolute;inset:0;background:linear-gradient(90deg,var(--team-dark),var(--team-mid) 45%,var(--team-dark))}
.team-body{position:relative;padding-top:66px}
.team h2{font-family:"Exo 2",sans-serif;font-weight:600;font-size:21px}
.team .lead{font-family:"Exo 2",sans-serif;font-weight:500;font-size:14px;line-height:22px;width:540px;margin:14px auto 0}
.values{display:flex;justify-content:center;gap:22px;margin-top:15px;font-weight:700;font-size:14.5px;letter-spacing:.2px}
.team-btn{width:122px;height:26px;line-height:26px;font-size:10.5px;margin-top:14px}
.contact{position:absolute;left:0;top:1004px;width:738px;height:172px;background:var(--white)}
.mark{position:absolute;left:197px;top:28px;width:122px;height:122px;border:2px solid var(--ink);border-radius:50%;
  display:flex;align-items:center;justify-content:center;font-family:"Exo 2",sans-serif;font-size:19px;font-weight:500;color:var(--ink)}
.contact-list{position:absolute;left:340px;top:44px;list-style:none;font-family:"Exo 2",sans-serif;font-weight:500;font-size:13px;line-height:15px;color:var(--ink)}
.contact-list li{display:flex;gap:14px;align-items:flex-start;margin-bottom:10px}
.contact-list svg{width:16px;height:16px;flex:none;margin-top:-1px}
.footer{position:absolute;left:0;top:1176px;width:738px;height:24px;background:var(--green);
  text-align:center;line-height:24px;font-size:7px;color:var(--ink)}
</style>
</head>
<body>
<header class="hero">
  <div class="hero-visual" role="img" aria-label="Glowing blue fibre optic strands"></div>
  <div class="brand"><span class="brand-dot"></span>Halverine</div>
  <nav class="nav">
    <a class="active" href="#">Home</a><a href="#">Venture Capital</a><a href="#">Private Credit</a><a href="#">Crypto</a><a href="#">Team</a><a href="#">Blog</a><a href="#">Contact Us</a>
  </nav>
  <h1 class="hero-title">Halverine Operates At The Intersection Of Technology And Novel Asset Classes.</h1>
  <a class="btn hero-btn" href="#">LEARN MORE</a>
</header>

<section class="lines">
  <div class="line-item">
    <svg viewBox="0 0 64 52" fill="none" stroke="var(--green-icon)" stroke-width="2"><circle cx="36" cy="14" r="11"/><path d="M36 8v12M33 11h5a2 2 0 010 4h-4a2 2 0 000 4h5"/><path d="M6 34h8v14H6zM14 36h14l6 4H24M14 46h22l20-10-3-3-17 7"/></svg>
    <h3>Venture Capital</h3>
    <p>We invest in early-stage startups led by founders who are passionate and knowledgeable about the....[+]</p>
  </div>
  <div class="line-item">
    <svg viewBox="0 0 64 52" fill="none" stroke="var(--green-icon)" stroke-width="2"><rect x="2" y="14" width="52" height="30" rx="3"/><circle cx="18" cy="29" r="6"/><path d="M38 24h20M42 30h20M38 36h18M12 6h48v30"/></svg>
    <h3>Private Credit</h3>
    <p>Halverine Private Credit provides capital to lending businesses that are focused on using technology...[+]t.</p>
  </div>
  <div class="line-item">
    <svg viewBox="0 0 64 52" fill="none" stroke="var(--green-icon)" stroke-width="2"><circle cx="32" cy="28" r="14"/><circle cx="32" cy="28" r="8"/><path d="M4 48l10-12 6 5 8-10M40 14l12-10M46 4h6v6"/></svg>
    <h3>Crypto</h3>
    <p>The Halverine Crypto Index tracks the top 15 cryptocurrencies weighted by market cap and rebalanced...[+]</p>
  </div>
</section>

<section class="about">
  <h2>About Us</h2>
  <p>Halverine operates three businesses that bridge technology and finance. We invest in pre-seed venture capital, and build software for the companies we invest in. We manage direct private credit funds that provide private credit capital to alternative private credit platforms, enabling them to finance the loans they originate. We create crypto funds for individuals, IRAs and institutions to get simple and easy access to cryptocurrencies.</p>
</section>

<section class="team">
  <div class="team-photo" role="img" aria-label="Black and white collage of team portraits"></div>
  <div class="team-body">
    <h2>Our Team</h2>
    <p class="lead">Our Highly Skilled Financial Consultants Are People Who Personifies The Very Qualities That Have Made Us Successful</p>
    <div class="values"><span>KNOWLEDGE.</span><span>EXPERIENCE.</span><span>ENTHUSIAM.</span><span>DEDICATION</span></div>
    <a class="btn team-btn" href="#">Read More About Us</a>
  </div>
</section>

<section class="contact">
  <div class="mark">Halverine</div>
  <ul class="contact-list">
    <li><svg viewBox="0 0 16 16" fill="none" stroke="var(--green-icon)" stroke-width="1.3"><path d="M8 14s-4-5-4-8a4 4 0 018 0c0 3-4 8-4 8z"/><circle cx="8" cy="6" r="1.5"/><path d="M2 14h12"/></svg><span>512 Meridian Avenue, Suite 804<br>Brookfield, NY 10118</span></li>
    <li><svg viewBox="0 0 16 16" fill="none" stroke="var(--green-icon)" stroke-width="1.3"><rect x="2" y="4" width="12" height="9"/><path d="M2 4l6 5 6-5"/></svg><span>info@halverine.vc</span></li>
    <li><svg viewBox="0 0 16 16" fill="none" stroke="var(--green-icon)" stroke-width="1.3"><circle cx="8" cy="8" r="6.5"/><path d="M6 5l1 2-1 1c.5 1 1.5 2 2 2l1-1 2 1-1 2c-3 0-5-3-5-5z"/></svg><span>555.014.2270</span></li>
  </ul>
</section>

<footer class="footer">Copyright © 2018 Halverine . All Rights Reserved</footer>
</body>
</html>
```